Verodex business card

Business card for sustainable investment company called "Verodex". Verodex is an exchange platform selling carbon credits between buyers and sellers. Carbon Credits are an environmental commodity for reducing global carbon emissions.

the card should obviously have our logo and the theme should be sustainability/environment mixed with a trading platform.

Contact Information for Business Card

Logo, Name, Title, Phone, Email

Colors
0054AA
0677BA
7BADD7
CADEEF
E8F1F8
0094D4
00A9DD
6FCCEA
C7EBF8
E9F6FB
00AB8E
00BBA5
67D7C9
C6EFE9
E9F9F6
59FF00
82FF00
B8FF75
E3FFCB
F4FFEA

```html
<!DOCTYPE html>
<html lang="en">
<head>
<meta charset="UTF-8">
<title>Verodex Business Card</title>
<link rel="stylesheet" href="https://fonts.googleapis.com/css2?family=Montserrat:wght@600&family=Poppins:wght@400;600&display=swap">
<style>
  :root {
    --backdrop: #a7a7a7;
    --card-white: #ffffff;
    --cyan: #33e0ee;
    --sky: #27b4ea;
    --blue: #1f7fe8;
    --navy: #1e2a44;
    --ink: #222833;
    --accent: #1e88e5;
    --card-w: 620px;
    --card-h: 354px;
    --radius: 30px;
  }
  * { box-sizing: border-box; margin: 0; padding: 0; }
  html, body {
    width: 1200px; height: 900px; overflow: hidden;
    background: var(--backdrop);
    font-family: "Poppins", sans-serif;
  }
  .stage {
    width: 1200px; height: 900px;
    display: flex; flex-direction: column;
    align-items: center; justify-content: center; gap: 56px;
  }
  .card {
    width: var(--card-w); height: var(--card-h);
    border-radius: var(--radius);
    position: relative; overflow: hidden;
    box-shadow: 0 10px 24px rgba(0,0,0,0.22);
  }
  .card--front {
    background: linear-gradient(35deg, var(--cyan) 0%, var(--sky) 50%, var(--blue) 100%);
    display: flex; align-items: center; justify-content: center;
  }
  .brand {
    display: flex; align-items: center; gap: 16px;
    font-family: "Montserrat", sans-serif; font-weight: 600;
    letter-spacing: 2px;
  }
  .brand__square { width: 30px; height: 30px; }
  .card--front .brand { color: var(--card-white); font-size: 44px; }
  .card--front .brand__square { background: var(--card-white); }

  .card--back { background: var(--card-white); }
  .card--back .brand {
    position: absolute; left: 50px; top: 56px;
    color: var(--navy); font-size: 44px;
  }
  .card--back .brand__square { background: var(--accent); width: 42px; height: 42px; }
  .person { position: absolute; left: 50px; top: 170px; }
  .person__name {
    font-weight: 600; font-size: 26px; letter-spacing: 1px;
    color: var(--accent); text-transform: uppercase; line-height: 1.1;
  }
  .person__title { font-size: 18px; color: var(--ink); }
  .contacts {
    position: absolute; left: 50px; top: 248px;
    list-style: none; display: flex; flex-direction: column; gap: 4px;
  }
  .contacts__item {
    display: flex; align-items: center; gap: 12px;
    font-size: 17px; color: var(--ink); line-height: 1.3;
  }
  .contacts__icon { width: 18px; height: 18px; flex: none; }
</style>
</head>
<body>
<main class="stage">
  <section class="card card--front" aria-label="Card front">
    <div class="brand"><span class="brand__square"></span><span>VERODEX</span></div>
  </section>

  <section class="card card--back" aria-label="Card back">
    <div class="brand"><span class="brand__square"></span><span>VERODEX</span></div>
    <div class="person">
      <p class="person__name">Daniel Harper</p>
      <p class="person__title">Managing Director</p>
    </div>
    <ul class="contacts">
      <li class="contacts__item">
        <svg class="contacts__icon" viewBox="0 0 24 24" fill="var(--accent)"><path d="M6.6 10.8a15 15 0 0 0 6.6 6.6l2.2-2.2a1 1 0 0 1 1-.25 11.4 11.4 0 0 0 3.6.57 1 1 0 0 1 1 1V20a1 1 0 0 1-1 1A17 17 0 0 1 3 4a1 1 0 0 1 1-1h3.5a1 1 0 0 1 1 1c0 1.25.2 2.45.57 3.57a1 1 0 0 1-.25 1z"/></svg>
        044-555 210 384
      </li>
      <li class="contacts__item">
        <svg class="contacts__icon" viewBox="0 0 24 24" fill="none" stroke="var(--accent)" stroke-width="2"><rect x="3" y="5" width="18" height="14" rx="1"/><path d="M3 6l9 7 9-7"/></svg>
        info@verodexmail.com
      </li>
      <li class="contacts__item">
        <svg class="contacts__icon" viewBox="0 0 24 24" fill="none" stroke="var(--accent)" stroke-width="2"><circle cx="12" cy="12" r="9"/><path d="M3 12h18M12 3c3 3 3 15 0 18M12 3c-3 3-3 15 0 18"/></svg>
        www.verodexsite.com
      </li>
    </ul>
  </section>
</main>
</body>
</html>
```